Brave Lotus - Fitness Retreat

Tri Fold Brochure & Double sided A4 version options, see attached mockup.

Target Market: Women 18-50, Asian mainly .

Kelvar Fitness Presents - Brave Lotus Fitness Retreats:

Something communicating the spirit of getting fit, being strong, eating healthy and strong sense of the feminine.

Industry/Entity Type

Fitness

```html
<!DOCTYPE html>
<html lang="en">
<head>
<meta charset="utf-8">
<title>Brave Lotus Fitness Retreats – Brochure</title>
<link rel="stylesheet" href="https://fonts.googleapis.com/css2?family=Noto+Serif:ital,wght@0,400;0,700;1,700&family=Roboto+Condensed:ital,wght@0,700;1,700&display=swap">
<style>
:root{
  --red:#b3131b;
  --red-dark:#7e0a10;
  --red-light:#d8262c;
  --cream:#fbf3dc;
  --paper:#ffffff;
  --ink:#2b2222;
  --muted:#6d6464;
  --gold:#f2c21a;
  --backdrop:#e9e9e7;
  --row:#fbeee0;
}
*{box-sizing:border-box;margin:0;padding:0}
html,body{width:1200px;height:819px;overflow:hidden}
body{background:var(--backdrop);font-family:"Noto Serif",Georgia,serif;color:var(--ink);position:relative}
.sheet{position:absolute;top:206px;width:575px;height:407px;background:var(--paper);box-shadow:0 4px 14px rgba(0,0,0,.18);overflow:hidden}
.sheet--outside{left:15px}
.sheet--inside{left:610px}

/* outside panels */
.panel{position:absolute;top:0;height:100%}
.panel--terms{left:0;width:192px;background:var(--cream);padding:14px 12px}
.panel--back{left:192px;width:191px}
.panel--cover{left:383px;width:192px}
.panel-heading{font-family:"Roboto Condensed",Arial,sans-serif;font-weight:700;color:var(--red);font-size:11px;letter-spacing:.3px;margin:8px 0 4px;text-transform:uppercase}
.panel-heading:first-child{margin-top:0}
.bullet-list{list-style:none;font-size:5.3px;line-height:1.55}
.bullet-list li{padding-left:7px;position:relative}
.bullet-list li::before{content:"";position:absolute;left:0;top:2.2px;width:3px;height:3px;border-radius:50%;background:var(--red)}

.back-hero{position:absolute;left:0;top:0;width:100%;height:190px;background:linear-gradient(160deg,var(--red-light),var(--red) 55%,var(--red-dark))}
.tagline{position:absolute;left:14px;top:18px;font-weight:700;color:#fff;font-size:11px;line-height:1.3;width:110px}
.price-tag{position:absolute;left:95px;top:48px;width:90px;height:110px}
.photo-strip{position:absolute;left:0;top:190px;width:100%;height:62px;display:flex;gap:3px;padding:0 6px;background:var(--paper)}
.photo{flex:1;border-radius:1px}
.photo--a{background:linear-gradient(160deg,#c9a184,#8c6a52)}
.photo--b{background:linear-gradient(160deg,#e6a0a8,#9c4a4e)}
.photo--c{background:linear-gradient(160deg,#b48d6e,#5d4634)}
.logo-row{position:absolute;left:0;top:252px;width:100%;height:62px;display:flex;align-items:center;justify-content:space-between;padding:0 14px}
.brand-mark{display:flex;align-items:center;gap:4px;font-family:"Roboto Condensed",Arial,sans-serif;font-weight:700;font-size:10px;color:var(--red)}
.brand-mark__square{width:10px;height:10px;background:var(--red)}
.partner-badge{width:34px;height:34px;border-radius:50%;border:2px solid #444}
.contact-block{position:absolute;left:0;top:314px;width:100%;height:93px;background:linear-gradient(160deg,var(--red),var(--red-dark));color:#fff;font-size:6px;line-height:1.55;padding:12px 18px}
.contact-block p+p{margin-top:7px}

.cover-title{position:absolute;left:0;top:20px;width:100%;text-align:center;font-family:"Roboto Condensed",Arial,sans-serif;font-style:italic;font-weight:700;color:var(--red);font-size:22px;letter-spacing:.5px}
.cover-sub{position:absolute;left:0;top:48px;width:100%;text-align:center;font-size:7px;color:var(--muted);letter-spacing:1px;text-transform:uppercase}
.cover-photo{position:absolute;left:14px;top:70px;width:164px;height:230px;background:linear-gradient(170deg,#d9c2ae,#a9805f 60%,#6e4e38)}
.cover-wave{position:absolute;left:0;bottom:0;width:100%;height:110px}
.cover-brand{position:absolute;right:14px;bottom:14px;font-family:"Roboto Condensed",Arial,sans-serif;font-weight:700;font-size:8px;color:var(--gold)}

/* inside */
.tips{position:absolute;left:12px;top:8px;width:288px;font-size:4.6px;line-height:1.42}
.tips p{margin-bottom:3.2px}
.tips b{color:var(--red)}
.tips-heading{font-family:"Roboto Condensed",Arial,sans-serif;font-weight:700;color:var(--red);font-size:6px;margin:5px 0 3px;text-transform:uppercase}
.photo-column{position:absolute;left:305px;top:10px;width:70px;display:flex;flex-direction:column;gap:9px}
.photo-column .photo{height:52px;flex:none}
.photo--d{background:linear-gradient(160deg,#caa78b,#7a5b46)}
.photo--e{background:linear-gradient(160deg,#4d4a47,#1f1d1c)}
.photo--f{background:linear-gradient(160deg,#9fc48a,#4f7a3c)}
.photo--g{background:linear-gradient(160deg,#8dbde0,#4b7a8f)}
.photo--h{background:linear-gradient(160deg,#a7b3b8,#5d6a6e)}

.activities{position:absolute;left:382px;top:0;width:193px;height:100%;border-left:1px solid #e6dcd6;padding:8px 6px}
.activities-title{font-family:"Roboto Condensed",Arial,sans-serif;font-style:italic;font-weight:700;color:var(--red);font-size:13px;text-align:center;margin-bottom:4px;text-transform:uppercase}
.schedule-head{display:flex;gap:3px;margin-bottom:2px}
.schedule-head span{background:var(--red);color:#fff;font-family:"Roboto Condensed",Arial,sans-serif;font-weight:700;font-size:6px;text-align:center;padding:1.5px 0;letter-spacing:1px}
.schedule-head span:first-child{width:24px}
.schedule-head span:last-child{flex:1}
.day{display:flex;gap:3px;margin-bottom:3px}
.day-name{width:24px;background:var(--row);display:flex;align-items:center;justify-content:center;font-family:"Roboto Condensed",Arial,sans-serif;font-weight:700;font-size:6px;color:var(--ink)}
.day-slots{flex:1;background:var(--row);padding:2px 3px;font-size:4.3px;line-height:1.45}
.day-slots b{color:var(--red);display:inline-block;width:14px}

.inside-band{position:absolute;left:0;bottom:0;width:575px;height:70px}
.slogan{position:absolute;left:20px;bottom:12px;width:460px;text-align:center;color:#fff;font-style:italic;font-weight:700;font-size:6.4px;line-height:1.5}
.band-brand{position:absolute;right:16px;bottom:16px;font-family:"Roboto Condensed",Arial,sans-serif;font-weight:700;font-size:8px;color:var(--gold)}
</style>
</head>
<body>

<section class="sheet sheet--outside" aria-label="Brochure outside">
  <div class="panel panel--terms">
    <h2 class="panel-heading">Inclusions</h2>
    <ul class="bullet-list">
      <li>Food and Accommodation</li>
      <li>Group transfer from airport or nearby hotel to retreat on Day 1</li>
      <li>Group transfer to airport or nearby hotel from retreat on Day 6</li>
      <li>All activities on the program</li>
      <li>Brave Lotus gift</li>
      <li>Pair of boxing gloves</li>
      <li>Brave Lotus Tank Top &amp; Workout Towel</li>
      <li>30 min Massage</li>
    </ul>
    <h2 class="panel-heading">Exclusions</h2>
    <ul class="bullet-list">
      <li>Flights to the island</li>
      <li>Travel insurance</li>
      <li>Bottled drinks such as water, soft drinks, beer</li>
      <li>Personal costs</li>
      <li>Extra tours, transport, massages, spa treatments outside the program</li>
    </ul>
    <h2 class="panel-heading">Terms &amp; Conditions</h2>
    <ul class="bullet-list">
      <li>Travel insurance is mandatory for the whole stay</li>
      <li>Please confirm any special dietary needs before booking. Please note we cannot guarantee meals free from every allergen on site.</li>
      <li>All clients must complete a <b>Fitness &amp; Health Assessment</b> form before arrival</li>
      <li>Instalment payments are possible. A deposit of $200 secures your place.</li>
      <li>Final payment is due 30 days prior to arrival date</li>
      <li>Cancellations within 30 days are non refundable</li>
      <li>The retreat may change the program due to weather or safety</li>
      <li>Personal expenses to be paid in cash at end of retreat</li>
      <li>We provide clean, safe and friendly conditions</li>
    </ul>
  </div>

  <div class="panel panel--back">
    <div class="back-hero">
      <p class="tagline">6 Days / 5 Nights Fitness, Fun, Friendship &amp; Adventure</p>
      <svg class="price-tag" viewBox="0 0 90 110" aria-label="Price 1,650 US dollars per person">
        <g transform="rotate(-22 45 55)">
          <line x1="45" y1="0" x2="45" y2="18" stroke="#fff" stroke-width="1"/>
          <path d="M30 28 L45 16 L60 28 L60 100 L30 100 Z" fill="#fff"/>
          <path d="M32 30 L45 19 L58 30 L58 98 L32 98 Z" fill="var(--red)"/>
          <circle cx="45" cy="28" r="3" fill="#fff"/>
          <text x="45" y="88" transform="rotate(-90 45 88)" fill="#fff" font-family="Noto Serif, serif" font-weight="700" font-size="14">$ 1,650 <tspan font-size="8">pp</tspan></text>
        </g>
      </svg>
    </div>
    <div class="photo-strip">
      <div class="photo photo--a" role="img" aria-label="Photo of women training outdoors"></div>
      <div class="photo photo--b" role="img" aria-label="Photo of a woman with pink boxing gloves"></div>
      <div class="photo photo--c" role="img" aria-label="Photo of a woman stretching in a fitness top"></div>
    </div>
    <div class="logo-row">
      <div class="brand-mark"><span class="brand-mark__square"></span>Kelvar Fitness</div>
      <div class="partner-badge" role="img" aria-label="Partner badge: Tidehouse Stays"></div>
    </div>
    <div class="contact-block">
      <p>hello@kelvarfitness.example<br>+62 812 0040 1188<br>www.kelvarfitness.example</p>
      <p>info@tidehouse.example<br>+62 812 0070 2299<br>www.tidehouse.example</p>
    </div>
  </div>

  <div class="panel panel--cover">
    <h1 class="cover-title">Brave Lotus</h1>
    <p class="cover-sub">Fitness Retreats</p>
    <div class="cover-photo" role="img" aria-label="Photo of a strong woman training on the beach"></div>
    <svg class="cover-wave" viewBox="0 0 192 110" preserveAspectRatio="none" aria-hidden="true">
      <path d="M0 40 C60 10 120 70 192 30 L192 110 L0 110 Z" fill="var(--red)"/>
      <path d="M0 46 C60 18 120 76 192 38" fill="none" stroke="var(--gold)" stroke-width="1.2"/>
    </svg>
    <span class="cover-brand">Kelvar Fitness</span>
  </div>
</section>

<section class="sheet sheet--inside" aria-label="Brochure inside">
  <div class="tips">
    <p><b>Training sessions :</b> 4 sets of workout gear as a minimum. Sports water bottle. Best to bring 2 pairs of shoes, one old pair for muddy conditions.</p>
    <p><b>Yoga &amp; Stretch sessions :</b> Comfortable stretch pants and tee's.</p>
    <p><b>Walks &amp; treks :</b> Workout gear works best. Bring gear, including sport shoes that you don't mind getting wet and dirty at times.</p>
    <p><b>Shoes :</b> We spend a lot of time outdoors, so pack suitable sandals or thongs.</p>
    <p><b>Everyday :</b> Preferably bring 2 pairs of sport shoes as this allows time for one pair to dry if necessary. Light weight casual clothes for the tropics. Long sleeve sweater and pants for the cool evenings. Hat, sunglasses, sunscreen, umbrella, insect repellent and a refillable water bottle.</p>
    <p><b>Volcano/Hot Springs :</b> It's very cool when you start, but you will soon be warm. Wear layers. A nylon wind jacket is a good idea. We can provide you with a walking stick. Swimming gear, day pack, small torch and a refillable drink bottle. Sport shoes are ok, but some people feel more comfortable in light hiking boots.</p>
    <p><b>Bits &amp; Pieces :</b> Bring an adaptor suitable for Indonesia if you need to use your charger. Reusable shopping bag or daypack is a good idea to help avoid plastic bags. Pack the camera. Check the batteries before you leave.</p>
    <p><b>Banned Narcotics :</b> Don't even think about packing them! You will be terminated from the property.</p>
    <h3 class="tips-heading">Handy Travel Hints</h3>
    <p><b>The Airport (International) :</b> Ensure that your passport is valid for 6 months with 1 empty page. Before you go through immigration you will have to pay the visa on arrival fee in cash. If you are unsure about the airport arrival process you might want to use a VIP arrival service. They will meet you in the arrivals hall and escort you through the visitor visa, customs and baggage process.</p>
    <p><b>Group Transfers :</b> Your package includes group transfers to the retreat from the airport or nearby hotel at approx. 2pm on Day 1. Group transfers at end of retreat are to airport or nearby hotel.</p>
    <p><b>Money :</b> Local currency is Rupiah and the exchange rate does fluctuate. ATM and currency exchange is available at the airport. (no facilities at the retreat) You will only need cash for your extras whilst on retreat.</p>
    <p><b>Drinking Water :</b> Only drink bottled water, including cleaning your teeth.</p>
    <p><b>Staying in Touch :</b> We have mobile phone reception, but no landlines or WiFi. Ensure that global roaming is organised in your phone BEFORE you leave home. If you prefer a local sim card, have your phone unlocked before you leave and buy one at the airport from a kiosk that sells drinks etc.</p>
    <p><b>Meals :</b> Meals are a delightful time at the retreat. We all eat together and our style is genuine village style Balinese food. Spicy vegetable, fish or chicken dishes accompany rice. Fruit is served with every meal. If you have a food allergy please let us know well before arrival.</p>
    <p><b>Alcohol :</b> The only alcohol we serve is the local beer. Bring your own wine as it is difficult and expensive to buy locally. We can provide juices, tonic and soda for you to mix with your own spirits.</p>
    <p><b>Safety :</b> Make sure you have travel insurance (compulsory for all of our guests). Please bring a photocopy of your passport photo page for local registration purposes. Be responsible about any medical conditions you may have. Pack your medications and prescriptions as necessary.</p>
  </div>

  <div class="photo-column">
    <div class="photo photo--d" role="img" aria-label="Photo of a woman training with a sandbag"></div>
    <div class="photo photo--e" role="img" aria-label="Photo of a woman flipping a large tyre"></div>
    <div class="photo photo--f" role="img" aria-label="Photo of women doing yoga in a garden"></div>
    <div class="photo photo--g" role="img" aria-label="Photo of a group jumping on a field"></div>
    <div class="photo photo--h" role="img" aria-label="Photo of a woman stretching on a black sand beach"></div>
  </div>

  <div class="activities">
    <h2 class="activities-title">Brave Lotus Activities</h2>
    <div class="schedule-head"><span>DAYS</span><span>ACTIVITIES</span></div>
    <div class="day"><div class="day-name">ONE</div><div class="day-slots">
      <b>2pm</b>Group Transfer from Airport or nearby Hotel<br><b>5pm</b>Settle into your Bungalow with a welcome Lemongrass tea<br><b>6pm</b>Time to get to know each other and Introduction to the program<br><b>7pm</b>Dinner Balinese Style</div></div>
    <div class="day"><div class="day-name">TWO</div><div class="day-slots">
      <b>6am</b>Stretching - Assessment - All Fitness Intro<br><b>8am</b>Breakfast<br><b>9am</b>Fun Jungle Trek Fitness adventure<br><b>12n</b>Lunch<br><b>2pm</b>Body Weight Management Work Shop<br><b>4pm</b>Muay Thai Strength &amp; Conditioning<br><b>7pm</b>Dinner</div></div>
    <div class="day"><div class="day-name">THREE</div><div class="day-slots">
      <b>3am</b>Departure for Mount Batur Sunrise Volcano Climb<br><b>9am</b>Rest at the Lakeside Hot Springs<br><b>12n</b>Lunch<br><b>2pm</b>Home Training Work Shop<br><b>4.30</b>Pilates<br><b>7pm</b>Dinner</div></div>
    <div class="day"><div class="day-name">FOUR</div><div class="day-slots">
      <b>7am</b>Breakfast<br><b>8.30</b>Interval Training on hills<br><b>12n</b>Lunch<br><b>2pm</b>Nutrition &amp; Diet Work Shop<br><b>4pm</b>Yoga<br><b>7pm</b>Dinner</div></div>
    <div class="day"><div class="day-name">FIVE</div><div class="day-slots">
      <b>6am</b>All Fitness - HIIT Strength &amp; Conditioning<br><b>8am</b>Breakfast<br><b>9am</b>Jungle Trek<br><b>12n</b>Lunch<br><b>2pm</b>Traditional Balinese Dance Class<br><b>7pm</b>Dinner</div></div>
    <div class="day"><div class="day-name">SIX</div><div class="day-slots">
      <b>6am</b>Final Training - 5 Fitness Elements - Final Challenge - Fitness Performance &amp; Review<br><b>8am</b>Breakfast<br><b>9am</b>Sister Talk / Motivational Speaking<br><b>12n</b>Farewell - Departure to Airport or next destination</div></div>
  </div>

  <svg class="inside-band" viewBox="0 0 575 70" preserveAspectRatio="none" aria-hidden="true">
    <path d="M0 22 C150 0 330 34 575 8 L575 70 L0 70 Z" fill="var(--red)"/>
    <path d="M0 26 C150 4 330 38 575 12" fill="none" stroke="var(--gold)" stroke-width="1.2"/>
  </svg>
  <p class="slogan">Be prepared to challenge yourself and have a lot of fun. Most importantly pack an open mind!<br>You are about to have a very unique experience.</p>
  <span class="band-brand">Kelvar Fitness</span>
</section>

</body>
</html>
```